Make attractive Packaging label for NUT BUTTERS jars

We at Velora Pantry are launching our own line of NUT BUTTERS. We will be serving them in GLASS JARS ready packaged. I need attractive luxurious design for glass jar and should be designed ready to print.
I have attached glass jar pictures and measurement sheet.
My company logo has been attached. Also company details can be found on our facebook page.
product will be

ALMOND BUTTER
CASHEW BUTTER
PEANUT BUTTER
HAZELNUT BUTTER.

Industry/Entity Type

Retail

```html
<!DOCTYPE html>
<html lang="en">
<head>
<meta charset="utf-8">
<title>Velora Pantry – Hazelnut Butter Jar Label</title>
<link href="https://fonts.googleapis.com/css2?family=Carlito:wght@400;700&family=Boogaloo&display=swap" rel="stylesheet">
<style>
  :root {
    --page: #ffffff;
    --cream: #fdfbec;
    --yellow: #f9d20a;
    --yellow-light: #fbe98a;
    --brown: #3b1f16;
    --brown-soft: #5a3222;
    --logo-brown: #8a5a1e;
    --ink: #111111;
    --white: #ffffff;
    --badge-orange: #f7941d;
    --badge-green: #8cc63f;
    --badge-green-deep: #5fb846;
  }
  * { margin: 0; padding: 0; box-sizing: border-box; }
  html, body { width: 1200px; height: 1000px; overflow: hidden; background: var(--page); }
  .canvas { position: relative; width: 1200px; height: 1000px; font-family: "Carlito", "Calibri", sans-serif; color: var(--ink); }
  .label-band { position: absolute; left: 0; top: 0; }

  .contact-list { list-style: none; font-size: 14px; line-height: 16px; }
  .contact-item { position: absolute; left: 36px; padding-left: 22px; white-space: nowrap; }
  .contact-item.address { top: 373px; }
  .contact-item.web { top: 408px; }
  .contact-item.mail { top: 431px; }
  .contact-item.phone { top: 456px; line-height: 15px; }
  .contact-icon { position: absolute; left: 0; top: 0; width: 14px; height: 16px; }

  .brand-name {
    position: absolute; left: 432px; top: 350px; width: 270px;
    font-family: "Carlito", sans-serif; font-weight: 700; font-size: 64px; line-height: 60px;
    color: var(--logo-brown); text-align: center;
  }

  .product-art {
    position: absolute; left: 582px; top: 458px; width: 204px; height: 140px;
    border-radius: 48% 52% 44% 56% / 50% 46% 54% 50%;
    background: radial-gradient(ellipse at 45% 45%, var(--brown-soft), var(--brown) 70%);
  }
  .product-name {
    position: absolute; left: 594px; top: 490px; transform: rotate(-9deg); transform-origin: left top;
    color: var(--white);
  }
  .product-name .nut { display: block; font-family: "Boogaloo", cursive; font-size: 46px; line-height: 44px; }
  .product-name .kind { display: block; font-family: "Carlito", sans-serif; font-size: 24px; letter-spacing: 2px; margin-left: 10px; }

  .shop-blurb { position: absolute; left: 838px; top: 492px; width: 322px; font-size: 14px; line-height: 18px; }
  .shop-blurb .line { display: block; text-align: justify; text-align-last: justify; }
  .shop-blurb .line.last { text-align-last: left; }
</style>
</head>
<body>
<div class="canvas">
  <svg class="label-band" width="1200" height="1000" viewBox="0 0 1200 1000" aria-hidden="true">
    <rect x="0" y="332" width="1197" height="272" fill="var(--cream)"/>
    <rect x="0" y="332" width="1197" height="18" fill="var(--yellow)"/>
    <polygon points="0,570 1197,425 1197,440 0,586" fill="var(--yellow-light)"/>
    <polygon points="0,586 1197,440 1197,604 0,604" fill="var(--yellow)"/>
    <g class="diet-badges">
      <circle cx="904" cy="397" r="34" fill="var(--white)" stroke="#333" stroke-width="2"/>
      <circle cx="904" cy="397" r="28" fill="var(--badge-orange)"/>
      <circle cx="999" cy="397" r="34" fill="var(--white)" stroke="#333" stroke-width="2"/>
      <circle cx="999" cy="397" r="28" fill="var(--badge-green)"/>
      <circle cx="1093" cy="397" r="34" fill="var(--white)" stroke="#333" stroke-width="2"/>
      <circle cx="1093" cy="397" r="28" fill="var(--badge-green-deep)"/>
    </g>
  </svg>

  <ul class="contact-list">
    <li class="contact-item address"><svg class="contact-icon" viewBox="0 0 14 16"><path d="M7 0C3.5 0 1 2.6 1 5.8 1 10 7 16 7 16s6-6 6-10.2C13 2.6 10.5 0 7 0zm0 8.3a2.4 2.4 0 1 1 0-4.8 2.4 2.4 0 0 1 0 4.8z" fill="var(--ink)"/></svg>Linden Court Arcade, North Upper Millers<br>Street, Dublin, Ireland</li>
    <li class="contact-item web"><svg class="contact-icon" viewBox="0 0 14 16"><circle cx="7" cy="8" r="6" fill="none" stroke="var(--ink)" stroke-width="2"/><path d="M1 8h12M7 2v12" stroke="var(--ink)" stroke-width="1.5"/></svg>www.velorapantry.ie</li>
    <li class="contact-item mail"><svg class="contact-icon" viewBox="0 0 14 16"><rect x="0" y="3" width="14" height="10" fill="var(--ink)"/><path d="M0 3l7 6 7-6" fill="none" stroke="var(--white)" stroke-width="1.4"/></svg>info@velorapantry.ie</li>
    <li class="contact-item phone"><svg class="contact-icon" viewBox="0 0 14 16"><path d="M3 1l3 1 1 4-2 1.5c.8 2 2 3.6 3.8 4.6L10.5 10l3 1.4-.5 3.4C7 15 1.5 8.5 1 2.5z" fill="var(--ink)"/></svg>353 85 402 7716<br>085 618 3390<br>085 402 7716</li>
  </ul>

  <div class="brand-name">Velora<br>Pantry</div>

  <div class="product-art" role="img" aria-label="Brown chocolate splash with whole and cracked hazelnuts and a green leaf"></div>
  <div class="product-name">
    <span class="nut">Hazelnut</span>
    <span class="kind">BUTTER</span>
  </div>

  <p class="shop-blurb">
    <span class="line">A unique Dublin's only exquisite edible Nuts, Seed</span>
    <span class="line">and Dried Fruit shop. From sweet and savoury</span>
    <span class="line">snacking nuts to raw healthy nuts &amp; seeds and Dried</span>
    <span class="line last">fruits.</span>
  </p>
</div>
</body>
</html>
```